New Brand - Website Design (4 Pages)

We are launching a new brand for electronic cigarettes. We already have logo and packaging done and would like a web design to go with it.

We are interested in the following deliverables:

1) Home Page Design
2) Check Out Design
3) How it Works Page
4) Secondary Template Page Design

Looking for a 60s modern look and something that is consistent with our logo and packaging.

Industry/Entity Type

Electronic

Requirements
Must have
• Consistent with logo and packaging (Use Logo Attached)
White background

Example (Functionality & Design): http://www.moltrafen.co.uk/
Example (Design): http://www.brendolark.com/

We want the design more like brendolark but the functionality the same as moltrafen.

Top Bar: Pale Dunes Kits; Cartridge Refills; How it Works; Contact; My Account; Checkout
Should not have
• Stock List or Search Bar or Newsletter Signup

```html
<!DOCTYPE html>
<html lang="en">
<head>
<meta charset="utf-8">
<title>Pale Dunes Kit</title>
<link rel="stylesheet" href="https://fonts.googleapis.com/css2?family=Signika:wght@300;400;600&display=swap">
<style>
:root{
  --ink:#1d1d1d;
  --text:#333;
  --sky:#8cd5f5;
  --band:#5f9fc0;
  --badge:#1a7fc3;
  --accent:#f0a020;
  --white:#fff;
  --footer:#ececec;
  --base:#2f2f2f;
  --thumb:#d8e1e5;
}
*{margin:0;padding:0;box-sizing:border-box}
html,body{width:1029px;height:1200px;overflow:hidden;background:var(--white)}
body{position:relative;font-family:"Signika",sans-serif;color:var(--text)}
h1,h2,h3{font-weight:400}
.abs{position:absolute}
.brand{left:82px;top:38px;display:flex;align-items:center;gap:10px}
.brand-dot{width:60px;height:68px;border-radius:50%;background:var(--sky)}
.brand-name{font-size:42px;font-weight:600;color:var(--ink);letter-spacing:1px}
.account-links{right:82px;top:22px;font-size:17px;color:var(--ink);display:flex;gap:12px;align-items:center}
.social{top:52px;width:38px;height:38px;border:2px solid var(--sky);border-radius:50%}
.hotline{right:80px;top:97px;font-size:25px;color:var(--accent)}
.hotline b{font-weight:600}
.nav{left:82px;top:132px;width:865px;height:39px;background:#000;color:var(--white);display:flex;justify-content:center;align-items:center;font-size:20px;gap:14px}
.nav span.sep{font-size:14px}
.stage{left:0;top:172px;width:1029px;height:773px;background:var(--sky)}
.card{left:82px;top:171px;width:865px;height:626px;background:var(--white)}
.side-title{left:117px;top:196px;font-size:28px;font-weight:600;color:var(--ink);letter-spacing:.5px}
.side-list{left:105px;top:240px;list-style:none;font-size:20px;font-weight:300;color:var(--ink)}
.side-list li{height:43px;line-height:34px;padding:0 12px}
.side-list li.active{background:var(--sky);color:var(--white);font-weight:600;border-radius:17px;width:153px}
.divider{left:301px;top:204px;width:2px;height:530px;background:var(--ink)}
.title{left:349px;top:191px;font-size:44px;font-weight:300;color:var(--ink);letter-spacing:1px;line-height:50px}
.rating{left:351px;top:238px;display:flex;align-items:center;gap:14px;font-size:16px;color:var(--ink)}
.stars{display:flex;gap:4px}
.desc{left:351px;top:273px;width:535px;font-size:15px;font-weight:300;line-height:17.8px;letter-spacing:.3px}
.product-shot{left:369px;top:415px;width:187px;height:201px;background:linear-gradient(135deg,#3a3a3a 0%,#1e1e1e 55%,#c8552f 100%)}
.thumb{top:638px;width:58px;height:58px;background:var(--thumb)}
.includes-title{left:608px;top:436px;font-size:20px;color:var(--ink);line-height:24px}
.includes{left:608px;top:472px;font-size:15px;font-weight:300;line-height:15px;list-style:none;letter-spacing:.3px}
.price{left:754px;top:586px;width:164px;height:164px;border-radius:50%;background:var(--sky)}
.price-text{left:754px;top:586px;width:164px;height:164px;display:flex;align-items:center;justify-content:center;padding:0 0 14px 8px;font-size:44px;font-weight:600;color:var(--white);letter-spacing:1px}
.cart-btn{left:651px;top:691px;width:222px;height:41px;border-radius:21px;background:var(--ink);color:var(--white);font-size:19px;font-weight:600;letter-spacing:1.5px;padding-left:14px;line-height:41px;overflow:hidden}
.cart-btn i{position:absolute;right:0;top:0;width:58px;height:41px;background:var(--white);border-radius:21px 0 0 21px;border:2px solid var(--ink)}
.band{left:2px;top:864px;width:1027px;height:36px;background:var(--band)}
.promise{top:836px;height:72px;display:flex;align-items:center;gap:6px;color:var(--white);font-size:21px;font-weight:600;letter-spacing:.5px}
.promise .disc{width:72px;height:72px;border-radius:50%;background:var(--badge);display:flex;align-items:center;justify-content:center;flex-direction:column;line-height:1}
.footer{left:0;top:945px;width:1029px;height:193px;background:var(--footer)}
.fcol{top:966px;color:var(--ink)}
.fcol h3{font-size:21px;font-weight:600;letter-spacing:.5px;line-height:24px;margin-bottom:10px}
.fcol ul{list-style:none;font-size:12.5px;line-height:15.2px}
.base{left:0;top:1138px;width:1029px;height:62px;background:var(--base);color:var(--white);font-size:13px;text-align:center;line-height:50px}
</style>
</head>
<body>
<div class="abs brand"><span class="brand-dot"></span><span class="brand-name">PALE DUNES</span></div>
<div class="abs account-links">
  <span>Sign up</span><span>|</span><span>Login</span><span>|</span>
  <svg width="22" height="18" viewBox="0 0 22 18"><path d="M1 2h4l3 10h10l2-7H7" fill="none" stroke="#1d1d1d" stroke-width="2"/><circle cx="9" cy="15.5" r="1.6" fill="#1d1d1d"/><circle cx="17" cy="15.5" r="1.6" fill="#1d1d1d"/></svg>
  <span>Checkout</span>
</div>
<span class="abs social" style="left:850px"></span>
<span class="abs social" style="left:909px"></span>
<div class="abs hotline">Call FREE Mon-Fri 8am-8pm: <b>0800 0612 487</b></div>

<nav class="abs nav">
  <span>Pale Dunes Kits</span><span class="sep">|</span><span>Cartridge Refills</span><span class="sep">|</span><span>How it Works</span><span class="sep">|</span><span>Contact</span><span class="sep">|</span><span>My Account</span>
</nav>

<div class="abs stage"></div>
<section class="abs card"></section>

<h2 class="abs side-title">PRODUCTS</h2>
<ul class="abs side-list">
  <li class="active">Pale Dunes Kit</li>
  <li>Cartridge Refills</li>
  <li>Batteries</li>
  <li>Charging Case</li>
  <li>USB Stick Charger</li>
  <li>Car Charger</li>
  <li>UK Mains Adaptor</li>
  <li>EU Charger</li>
</ul>
<div class="abs divider"></div>

<h1 class="abs title">PALE DUNES KIT</h1>
<div class="abs rating">
  <div class="stars">
    <svg width="108" height="20" viewBox="0 0 108 20">
      <defs><path id="star" d="M10 1l2.7 5.8 6.3.7-4.7 4.3 1.3 6.2L10 14.9 4.4 18l1.3-6.2L1 7.5l6.3-.7z"/></defs>
      <use href="#star" fill="#f0a020"/>
      <use href="#star" x="27" fill="#f0a020"/>
      <use href="#star" x="54" fill="#f0a020"/>
      <use href="#star" x="81" fill="#f0a020"/>
    </svg>
    <svg width="22" height="20" viewBox="0 0 22 20"><path d="M10 1l2.7 5.8 6.3.7-4.7 4.3 1.3 6.2L10 14.9 4.4 18l1.3-6.2L1 7.5l6.3-.7z" fill="none" stroke="#f0a020" stroke-width="1.3"/></svg>
  </div>
  <span>|</span><span>5 reviews</span><span>|</span><span>Write review</span>
</div>
<p class="abs desc">Product info putate diam. Nullam mattis ipsum eget risus lobortis venenatis. Nunc elit nulla, vehicula nec eros quis, scelerisque pulvinar sem. Etiam porta enim a aliquet malesuada. Sed vehicula risus purus, et fermentum urna sodales in. Interdum et malesuada fames ac ante ipsum primis in faucibus. Nunc sodales lorem elit, ac venenatis magna rhoncus vel. Praesent magna arcu, faucibus nec placerat vitae, dapibus nec eros.</p>

<div class="abs product-shot" role="img" aria-label="Pale Dunes kit packaging box"></div>
<div class="abs thumb" style="left:371px"></div>
<div class="abs thumb" style="left:435px"></div>
<div class="abs thumb" style="left:499px"></div>

<h3 class="abs includes-title">Product includes:</h3>
<ul class="abs includes">
  <li>• 2 rechargeable Drift batteries,</li>
  <li>• Portable charging case,</li>
  <li>• Handy travelling case,</li>
  <li>• USB &amp; UK mains chargers,</li>
  <li>• 5 flavour cartridge refills - equivalent to</li>
  <li>150 cigarettes.</li>
</ul>

<div class="abs price"></div>
<div class="abs price-text">£49.99</div>
<div class="abs cart-btn">ADD TO CART<i></i></div>

<div class="abs band"></div>
<div class="abs promise" style="left:100px"><span class="disc"><span style="font-size:36px">30</span><span style="font-size:20px">DAY</span></span>MONEY BACK PROMISE*</div>
<div class="abs promise" style="left:418px"><span class="disc"><svg width="40" height="40" viewBox="0 0 40 40"><path d="M20 4l16 7v16l-16 8-16-8V11z M4 11l16 8 16-8 M20 19v16" fill="none" stroke="#fff" stroke-width="3" stroke-linejoin="round"/></svg></span>FREE SHIPPING</div>
<div class="abs promise" style="left:675px"><span class="disc"><svg width="36" height="46" viewBox="0 0 36 46"><path d="M10 24l-6 18 7-3 4 6 4-13 M26 24l6 18-7-3-4 6-4-13" fill="#fff"/><circle cx="18" cy="16" r="13" fill="#fff"/></svg></span>ONE YEAR WARRANTY*</div>

<footer class="abs footer"></footer>
<div class="abs fcol" style="left:161px"><h3>PRODUCTS</h3><ul><li>Pale Dunes Kit</li><li>Cartridge Refill</li><li>Charger</li><li>Battery</li><li>Case</li><li>Other Product</li></ul></div>
<div class="abs fcol" style="left:357px"><h3>ABOUT ELECTRONIC<br>CIGARETTES</h3><ul><li>How it works</li><li>Statistic</li><li>Money saved</li><li>Healthy choice</li><li>Science</li></ul></div>
<div class="abs fcol" style="left:626px"><h3>ORDERING</h3><ul><li>Order</li><li>Checkout</li><li>Shipping</li><li>Returns</li></ul></div>
<div class="abs fcol" style="left:809px"><h3>ABOUT US</h3><ul><li>Pale Dunes</li><li>Partners</li><li>Recources</li></ul></div>
<div class="abs base">Copyright 2013 Pale Dunes - Terms &amp; Conditions | Privacy Policy</div>
</body>
</html>
```